Business card design for my company.
I would like the card's background colour to be black. You can also see our web site to get an idea of our brand. https://www.tmwhomecrafting.com.au/
- Name
- Email

```html
<!DOCTYPE html>
<html lang="en">
<head>
<meta charset="utf-8">
<title>TMW Home Crafting — Business Card</title>
<link href="https://fonts.googleapis.com/css2?family=Poppins:wght@400;500&display=swap" rel="stylesheet">
<style>
  :root{
    --backdrop:#8e8e8e;
    --card-black:#1e1e1e;
    --brand-green:#0b9444;
    --ink-white:#ffffff;
    --emboss-grey:#3b3b3b;
  }
  *{box-sizing:border-box;margin:0;padding:0}
  html,body{width:1200px;height:1122px;overflow:hidden}
  body{background:var(--backdrop);font-family:'Poppins',sans-serif;position:relative}
  .card{position:absolute;left:220px;width:760px;height:434px;border-radius:28px;background:var(--card-black);overflow:hidden;box-shadow:0 8px 22px rgba(0,0,0,.25)}
  .card--front{top:80px}
  .card--back{top:600px}
  .wordmark{position:absolute;display:flex;align-items:center;gap:14px;font-weight:500;letter-spacing:.04em;white-space:nowrap}
  .wordmark__square{width:22px;height:22px}
  .card--front .wordmark{left:50%;top:50%;transform:translate(-50%,-50%);font-size:40px;color:var(--emboss-grey)}
  .card--front .wordmark__square{background:var(--emboss-grey)}
  .card--back .wordmark{left:40px;top:190px;font-size:27px;color:var(--ink-white)}
  .card--back .wordmark__square{background:var(--brand-green)}
  .divider{position:absolute;inset:0;width:760px;height:434px}
  .details{position:absolute;left:500px;top:96px;color:var(--ink-white)}
  .details__name{font-size:27px;font-weight:500;letter-spacing:.03em;line-height:1.1}
  .details__role{font-size:15px;margin-top:4px}
  .contact{list-style:none;margin-top:34px}
  .contact__item{display:flex;align-items:center;gap:10px;font-size:14px;line-height:1.95}
  .contact__icon{width:14px;height:14px;flex:none;fill:var(--ink-white)}
</style>
</head>
<body>
  <section class="card card--front" aria-label="Card front">
    <div class="wordmark"><span class="wordmark__square"></span>TMW Home Crafting</div>
  </section>

  <section class="card card--back" aria-label="Card back">
    <svg class="divider" viewBox="0 0 760 434" aria-hidden="true">
      <polygon points="355,0 760,0 760,434 500,434 425,230 450,170 400,150" fill="var(--brand-green)"/>
      <polyline points="340,0 390,150 440,170 415,230 490,434" fill="none" stroke="var(--ink-white)" stroke-width="7"/>
      <polyline points="325,0 380,156 428,174 402,232 476,434" fill="none" stroke="var(--brand-green)" stroke-width="4"/>
    </svg>
    <div class="wordmark"><span class="wordmark__square"></span>TMW Home Crafting</div>
    <div class="details">
      <p class="details__name">LIAM CASTELL</p>
      <p class="details__role">General Manager</p>
      <ul class="contact">
        <li class="contact__item"><svg class="contact__icon" viewBox="0 0 24 24"><path d="M6.6 10.8a15.1 15.1 0 0 0 6.6 6.6l2.2-2.2a1 1 0 0 1 1-.25 11.4 11.4 0 0 0 3.6.57 1 1 0 0 1 1 1V20a1 1 0 0 1-1 1A17 17 0 0 1 3 4a1 1 0 0 1 1-1h3.5a1 1 0 0 1 1 1c0 1.25.2 2.45.57 3.57a1 1 0 0 1-.25 1z"/></svg>0400 512 738</li>
        <li class="contact__item"><svg class="contact__icon" viewBox="0 0 24 24"><path d="M2 5h20v14H2z M3 6l9 7 9-7" fill="var(--ink-white)" stroke="var(--brand-green)" stroke-width="1.5"/></svg>info@tmwhomecrafting.com.au</li>
        <li class="contact__item"><svg class="contact__icon" viewBox="0 0 24 24"><circle cx="12" cy="12" r="10"/><path d="M2 12h20M12 2c3 3 3 17 0 20M12 2c-3 3-3 17 0 20" fill="none" stroke="var(--brand-green)" stroke-width="1.5"/></svg>tmwhomecrafting.com.au</li>
        <li class="contact__item"><svg class="contact__icon" viewBox="0 0 24 24"><path d="M12 2a7 7 0 0 0-7 7c0 5 7 13 7 13s7-8 7-13a7 7 0 0 0-7-7zm0 9.5A2.5 2.5 0 1 1 12 6.5a2.5 2.5 0 0 1 0 5z"/></svg>Riverton, Tasmania, Australia</li>
      </ul>
    </div>
  </section>
</body>
</html>
```